FinTech company looking to revamp and expand client-facing interface for our financial models

Pellworth Engines currently has a very simple website that allows clients to interact with our financial models. We are looking to completely redesign the current site and add several extra pages to provide extra functionality. We want the design to have a modern, slick feel, that will work on both a desktop or a tablet. It should be straightforward for clients to move between different pages at any time, and clear from the layout how to interact with the more advanced features. We have included screenshots of existing pages in the attached design brief, as well as sketches of the functionality required by the new pages, but can't provide a direct link to the current site.
Target Market(s)
Professional investors that will be paying to access the interface
Industry/Entity Type
Finance
Number of Pages Required
4 page
Colors
Designer to choose colors to be used in the design.
Look and feel
Each slider illustrates characteristics of the customer's brand and the style your logo design should communicate.

```html
<!DOCTYPE html>
<html lang="en">
<head>
<meta charset="utf-8">
<title>QVANT – ETF Pairs</title>
<link rel="stylesheet" href="https://fonts.googleapis.com/css2?family=Montserrat:wght@500;600;700&family=Open+Sans:wght@400;600;700&family=Roboto:wght@400&display=swap">
<style>
  :root{
    --frame:#e6e6e6;
    --page:#ffffff;
    --backdrop:#ececec;
    --navy:#003366;
    --navy-deep:#0a3563;
    --teal:#00766a;
    --ink:#111111;
    --ink-soft:#222222;
    --tab-dark:#1a1a1a;
    --overlay:rgba(30,74,122,0.93);
    --panel:#1d4a7a;
    --white:#ffffff;
    --rule:#e2e2e2;
  }
  *{box-sizing:border-box;margin:0;padding:0}
  html,body{width:1200px;height:706px;overflow:hidden;background:var(--frame)}
  body{position:relative;font-family:"Open Sans",Arial,sans-serif}
  .page{position:absolute;left:14px;top:14px;width:1172px;height:678px;background:var(--backdrop);overflow:hidden}
  .abs{position:absolute}

  /* top navigation */
  .topbar{left:0;top:0;width:1172px;height:55px;background:var(--page);box-shadow:0 4px 10px rgba(0,0,0,.08)}
  .brand{left:53px;top:0;height:55px;line-height:55px;font:700 17px "Montserrat",sans-serif;color:var(--ink);letter-spacing:.3px}
  .horizon{top:0;height:55px;display:flex;align-items:center;justify-content:center;font:700 13px "Montserrat",sans-serif;color:var(--ink);border-right:1px solid var(--rule)}
  .horizon.active{background:var(--navy);color:var(--white)}
  .mainnav{top:0;height:55px;display:flex;align-items:center;justify-content:center;gap:8px;font:700 12.5px "Montserrat",sans-serif;color:var(--ink);border-left:1px solid var(--rule)}
  .mainnav.active{background:var(--navy);color:var(--white)}
  .mainnav svg{width:22px;height:22px}

  /* tabs */
  .tab{display:flex;align-items:center;justify-content:center;background:var(--page);font:700 12px "Montserrat",sans-serif;color:#333;border-radius:4px 4px 0 0;box-shadow:0 -1px 4px rgba(0,0,0,.06)}
  .tab.short{top:111px;height:33px}
  .tab.tall{top:101px;height:43px;padding-bottom:8px}
  .tab.current{top:93px;height:51px;background:var(--tab-dark);color:var(--white);padding-bottom:16px}
  .tab-more{left:1084px;top:111px;width:37px;height:33px;background:var(--page);display:flex;align-items:center;justify-content:center;border-radius:4px 4px 0 0}
  .tab-add{left:1126px;top:111px;width:37px;height:33px;background:var(--navy);display:flex;align-items:center;justify-content:center;border-radius:4px 4px 0 0}

  /* content */
  .content{left:0;top:143px;width:1172px;height:535px;background:#f4f4f4}
  .export{left:1061px;top:194px;font:700 16px "Open Sans",sans-serif;color:var(--navy);display:flex;align-items:center;gap:6px}

  .grid{left:83px;top:217px;width:1071px;border-radius:6px;overflow:hidden;background:var(--page);box-shadow:0 2px 8px rgba(0,0,0,.08)}
  .row{display:flex;height:64px;border-bottom:1px solid #eee}
  .row.head{background:#0f4c81;color:var(--white);font:600 15px "Open Sans",sans-serif}
  .cell{display:flex;align-items:center;flex:none;padding:0 8px;font:400 14.5px "Roboto",Arial,sans-serif;color:var(--ink-soft);line-height:1.25}
  .head .cell{justify-content:center;font:600 15.5px "Open Sans",sans-serif;color:var(--white)}
  .head .cell.deep{background:var(--navy-deep)}
  .head .cell.teal{background:var(--teal)}
  .c-id{width:111px;gap:6px;padding-left:14px}
  .c-sector{width:110px}
  .c-time{width:107px}
  .c-q{width:78px}
  .c-s{width:83px}
  .star{width:18px;height:18px}

  /* filter overlay */
  .filters{left:0;top:143px;width:1112px;height:535px;background:var(--overlay)}
  .filters-title{left:0;top:80px;width:1112px;text-align:center;font:700 19px "Open Sans",sans-serif;color:var(--white);padding-right:14px}
  .f-label{font:600 16.5px "Open Sans",sans-serif;color:var(--white);height:28px;line-height:28px}
  .f-input{width:167px;height:28px;background:var(--white);border-radius:4px;font:400 16px "Open Sans",sans-serif;color:var(--ink);line-height:28px;padding-left:13px;box-shadow:inset 0 1px 2px rgba(0,0,0,.25)}
  .search{left:484px;top:258px;width:143px;height:47px;border:2px solid var(--white);border-radius:5px;display:flex;align-items:center;justify-content:center;font:700 14.5px "Open Sans",sans-serif;color:var(--white)}

  .close-tab{left:1112px;top:295px;width:46px;height:231px;background:var(--panel);border-radius:0 4px 4px 0;display:flex;align-items:center;justify-content:center}
  .close-tab span{transform:rotate(-90deg);white-space:nowrap;font:600 16px "Open Sans",sans-serif;color:var(--white);letter-spacing:.4px}
  .close-knob{left:1146px;top:399px;width:24px;height:24px;border-radius:50%;background:var(--navy);border:2px solid var(--white);display:flex;align-items:center;justify-content:center}
</style>
</head>
<body>
<div class="page">

  <header class="abs topbar">
    <div class="abs brand">QVANT</div>
    <div class="abs horizon active" style="left:166px;width:83px">250D</div>
    <div class="abs horizon" style="left:249px;width:83px">83D</div>
    <div class="abs horizon" style="left:332px;width:83px">42D</div>

    <div class="abs mainnav active" style="left:697px;width:129px">
      <svg viewBox="0 0 24 24" fill="none" stroke="#fff" stroke-width="2"><path d="M3 11 12 3l9 8"/><path d="M5 10v10h5v-6h4v6h5V10"/></svg>MODELS
    </div>
    <div class="abs mainnav" style="left:826px;width:164px">
      <svg viewBox="0 0 24 24" fill="#111"><circle cx="12" cy="12" r="3"/><circle cx="12" cy="4" r="1.6"/><circle cx="12" cy="20" r="1.6"/><circle cx="4" cy="12" r="1.6"/><circle cx="20" cy="12" r="1.6"/><circle cx="6.3" cy="6.3" r="1.6"/><circle cx="17.7" cy="17.7" r="1.6"/><circle cx="17.7" cy="6.3" r="1.6"/><circle cx="6.3" cy="17.7" r="1.6"/></svg>SENSITIVITIES
    </div>
    <div class="abs mainnav" style="left:990px;width:182px">
      <svg viewBox="0 0 24 24" fill="none" stroke="#111" stroke-width="1.8"><path d="m12 2.5 2.9 6.1 6.6.8-4.9 4.6 1.3 6.6L12 17.3l-5.9 3.3 1.3-6.6-4.9-4.6 6.6-.8z"/></svg>FAVOURITES
    </div>
  </header>

  <nav>
    <div class="abs tab short" style="left:51px;width:143px">EQUITIES</div>
    <div class="abs tab short" style="left:198px;width:143px">ETFS</div>
    <div class="abs tab tall" style="left:346px;width:143px">PAIRS</div>
    <div class="abs tab tall" style="left:641px;width:143px">FACTORS</div>
    <div class="abs tab short" style="left:789px;width:143px">NEW TAB TITLE #1</div>
    <div class="abs tab short" style="left:937px;width:143px">NEW TAB TITLE #2</div>
    <div class="abs tab-more"><svg width="14" height="18" viewBox="0 0 14 18"><path d="M3 2l8 7-8 7" fill="none" stroke="#999" stroke-width="3"/></svg></div>
    <div class="abs tab-add"><svg width="22" height="22" viewBox="0 0 22 22" fill="none" stroke="#fff" stroke-width="1.8"><circle cx="11" cy="11" r="9.5"/><path d="M11 6v10M6 11h10"/></svg></div>
  </nav>

  <main class="abs content" style="top:144px"></main>

  <div class="abs export">
    <svg width="24" height="22" viewBox="0 0 24 22" fill="none" stroke="#003366" stroke-width="2"><path d="M10 4H3v16h16v-6"/><path d="M9 14c1-6 5-8 11-8"/><path d="M16 2l5 4-5 4"/></svg>Export
  </div>

  <section class="abs grid">
    <div class="row head">
      <div class="cell c-id deep" style="justify-content:center">ID ⌄</div>
      <div class="cell c-sector deep">Sector</div>
      <div class="cell c-time deep">Time</div>
      <div class="cell c-q">Quality</div>
      <div class="cell c-s">Stat 1</div>
      <div class="cell c-s">Stat 2</div>
      <div class="cell c-s">Stat 3</div>
      <div class="cell c-s">Stat 4</div>
      <div class="cell c-s">Stat 5</div>
      <div class="cell c-s">Stat 6</div>
      <div class="cell c-s">Stat 7</div>
      <div class="cell c-s teal">Stat 8</div>
    </div>
    <div class="row">
      <div class="cell c-id"><svg class="star" viewBox="0 0 24 24" fill="none" stroke="#333" stroke-width="1.6"><path d="m12 2.5 2.9 6.1 6.6.8-4.9 4.6 1.3 6.6L12 17.3l-5.9 3.3 1.3-6.6-4.9-4.6 6.6-.8z"/></svg>Model 1</div>
      <div class="cell c-sector">Materials</div>
      <div class="cell c-time">2019-07-03 12:15:00.000</div>
      <div class="cell c-q">30.2288</div><div class="cell c-s">2.01574</div><div class="cell c-s">23.305</div><div class="cell c-s">-0.149368</div><div class="cell c-s">22.3054</div><div class="cell c-s">4.63714</div><div class="cell c-s">0.945706</div><div class="cell c-s">2.81949</div><div class="cell c-s">2.60858</div>
    </div>
    <div class="row">
      <div class="cell c-id"><svg class="star" viewBox="0 0 24 24" fill="none" stroke="#333" stroke-width="1.6"><path d="m12 2.5 2.9 6.1 6.6.8-4.9 4.6 1.3 6.6L12 17.3l-5.9 3.3 1.3-6.6-4.9-4.6 6.6-.8z"/></svg>Model 2</div>
      <div class="cell c-sector">Industrials</div>
      <div class="cell c-time">2019-07-03 12:15:00.000</div>
      <div class="cell c-q">32.8694</div><div class="cell c-s">0.87307</div><div class="cell c-s">32.185</div><div class="cell c-s">-0.033692</div><div class="cell c-s">33.9911</div><div class="cell c-s">11.5693</div><div class="cell c-s">-0.472968</div><div class="cell c-s">-0.830458</div><div class="cell c-s">6.80617</div>
    </div>
    <div class="row">
      <div class="cell c-id"><svg class="star" viewBox="0 0 24 24" fill="none" stroke="#333" stroke-width="1.6"><path d="m12 2.5 2.9 6.1 6.6.8-4.9 4.6 1.3 6.6L12 17.3l-5.9 3.3 1.3-6.6-4.9-4.6 6.6-.8z"/></svg>Model 3</div>
      <div class="cell c-sector">Consumer Discretionary</div>
      <div class="cell c-time">2019-07-03 12:15:00.000</div>
      <div class="cell c-q">1.66002</div><div class="cell c-s">-0.569222</div><div class="cell c-s">159.814</div><div class="cell c-s">0.0252328</div><div class="cell c-s">172.616</div><div class="cell c-s">10.2875</div><div class="cell c-s">-0.750396</div><div class="cell c-s">-0.385309</div><div class="cell c-s">4.69133</div>
    </div>
    <div class="row">
      <div class="cell c-id"><svg class="star" viewBox="0 0 24 24" fill="#333"><path d="m12 2.5 2.9 6.1 6.6.8-4.9 4.6 1.3 6.6L12 17.3l-5.9 3.3 1.3-6.6-4.9-4.6 6.6-.8z"/></svg>Model 4</div>
      <div class="cell c-sector">Information Technology</div>
      <div class="cell c-time">2019-07-03 12:15:00.000</div>
      <div class="cell c-q">45.6856</div><div class="cell c-s">0.412148</div><div class="cell c-s">202.488</div><div class="cell c-s">0.0084923</div><div class="cell c-s">205.834</div><div class="cell c-s">11.9094</div><div class="cell c-s">-0.137913</div><div class="cell c-s">0.449595</div><div class="cell c-s">3.85106</div>
    </div>
    <div class="row" style="border-bottom:none">
      <div class="cell c-id"><svg class="star" viewBox="0 0 24 24" fill="#333"><path d="m12 2.5 2.9 6.1 6.6.8-4.9 4.6 1.3 6.6L12 17.3l-5.9 3.3 1.3-6.6-4.9-4.6 6.6-.8z"/></svg>Model 5</div>
      <div class="cell c-sector">Information Technology</div>
      <div class="cell c-time">2019-07-03 12:15:00.000</div>
      <div class="cell c-q">75.7733</div><div class="cell c-s">7.06728</div><div class="cell c-s">188.605</div><div class="cell c-s">0.016913</div><div class="cell c-s">161.665</div><div class="cell c-s">3.82241</div><div class="cell c-s">0.981019</div><div class="cell c-s">1.29847</div><div class="cell c-s">3.34927</div>
    </div>
  </section>

  <section class="abs filters">
    <div class="abs filters-title">FILTERS</div>

    <div class="abs f-label" style="left:199px;top:143px">Quality</div>
    <div class="abs f-label" style="left:278px;top:143px">Threshold:</div>
    <div class="abs f-input" style="left:371px;top:143px">-10</div>
    <div class="abs f-label" style="left:578px;top:143px">Abs. Stat</div>
    <div class="abs f-label" style="left:656px;top:143px">Threshold:</div>
    <div class="abs f-input" style="left:749px;top:143px">-10</div>

    <div class="abs f-label" style="left:199px;top:198px">Time</div>
    <div class="abs f-label" style="left:278px;top:198px">Threshold:</div>
    <div class="abs f-input" style="left:371px;top:198px">-10</div>
    <div class="abs f-label" style="left:578px;top:198px">Stat</div>
    <div class="abs f-label" style="left:656px;top:198px">Threshold:</div>
    <div class="abs f-input" style="left:749px;top:198px">-10</div>

    <div class="abs search">SEARCH</div>
  </section>

  <div class="abs close-tab"><span>CLOSE FILTERS</span></div>
  <div class="abs close-knob"><svg width="12" height="12" viewBox="0 0 12 12" fill="none" stroke="#fff" stroke-width="2"><path d="M11 6H2M6 2 2 6l4 4"/></svg></div>

  <div class="abs tab current" style="left:494px;width:143px">ETF PAIRS</div>
  <svg class="abs" style="left:609px;top:114px" width="22" height="30" viewBox="0 0 22 30">
    <path d="M7 2.5c1 0 2 .8 2 2v9l1-.2v-2c0-1 .8-1.6 1.7-1.6s1.7.7 1.7 1.6v1.2c.3-.7 1-1 1.7-1 .9 0 1.6.7 1.6 1.6v1.4c.3-.5.8-.8 1.4-.8.9 0 1.6.7 1.6 1.6v6.2c0 3.5-2.6 6.5-6 6.5h-2.6c-2 0-3.4-1-4.6-2.7L2 19c-.6-.9-.3-2 .6-2.5.8-.4 1.7-.2 2.3.5L5 18V4.5c0-1.2.9-2 2-2z" fill="#fff" stroke="#111" stroke-width="1.2"/>
  </svg>

</div>
</body>
</html>
```